Web Developer Needs a Business Card Design

I need a personal business card design that represents me as a web developer for potential employers. I would like the background to be a dark color on the front for contrast with my logo and name. The back will have all my information along with a smaller version of the logo. I want something with a modern look and feel, not too conservative. This will be used for potential employers and freelance work.

Industry/Entity Type

Business

Contact Information for Business Card

Front should have my logo and name. The back should have all my personal information which would include: name: Tom Varulek, phone: 570-614-3098, email: tomvarulek@quillbox.net, website url: www.tomvarulek.net, logo, web developer.

Font styles to use
Sans Serif

Requirements
Must have
• Must include my logo. The color palette base color will be the logo color.

```html
<!DOCTYPE html>
<html lang="en">
<head>
<meta charset="utf-8">
<title>Tom Varulek – Business Card</title>
<link rel="stylesheet" href="https://fonts.googleapis.com/css2?family=Source+Sans+3:ital,wght@0,400;0,600;1,400;1,700&display=swap">
<style>
  :root {
    --page-bg: #161616;
    --card-bg: #0c0c0c;
    --card-sheen: #1c1c1c;
    --accent: #7fcfb8;
    --accent-dark: #5fae99;
    --text-light: #f2f2f2;
    --text-muted: #d9d9d9;
  }
  * { box-sizing: border-box; margin: 0; padding: 0; }
  html, body {
    width: 1200px;
    height: 864px;
    overflow: hidden;
    background: var(--page-bg);
    font-family: "Source Sans 3", "Myriad Pro", Arial, sans-serif;
  }
  .stage {
    width: 1200px;
    height: 864px;
    display: flex;
    align-items: center;
    justify-content: center;
    gap: 40px;
  }
  .card {
    position: relative;
    width: 540px;
    height: 309px;
    background: linear-gradient(160deg, var(--card-sheen) 0%, var(--card-bg) 55%);
    border-radius: 3px;
    overflow: hidden;
    box-shadow: 0 10px 30px rgba(0,0,0,.6);
  }

  /* Mark: plain circle + name */
  .brand {
    display: flex;
    flex-direction: column;
    align-items: center;
    gap: 12px;
  }
  .brand-circle {
    width: 62px;
    height: 62px;
    border-radius: 50%;
    border: 5px solid var(--accent);
  }
  .brand-name {
    color: var(--text-light);
    font-size: 25px;
    font-weight: 400;
    letter-spacing: .5px;
    text-transform: uppercase;
  }

  /* Front */
  .card--front {
    display: flex;
    align-items: center;
    justify-content: center;
  }

  /* Back */
  .card--back .brand {
    position: absolute;
    left: 58px;
    top: 86px;
  }
  .card--back .brand-circle { width: 56px; height: 56px; border-width: 5px; }
  .card--back .brand-name { font-size: 23px; }

  .contact {
    position: absolute;
    left: 300px;
    top: 82px;
    padding-left: 14px;
    border-left: 3px dotted var(--accent);
    height: 112px;
  }
  .contact-name {
    color: var(--accent);
    font-size: 19px;
    font-weight: 700;
    font-style: italic;
    line-height: 1;
  }
  .contact-role {
    color: var(--text-muted);
    font-size: 14px;
    font-style: italic;
    margin-top: 2px;
    margin-bottom: 10px;
  }
  .contact-list { list-style: none; }
  .contact-item {
    display: flex;
    align-items: center;
    gap: 9px;
    color: var(--text-light);
    font-size: 14px;
    line-height: 1;
    margin-bottom: 5px;
  }
  .contact-icon {
    width: 14px;
    height: 14px;
    border-radius: 3px;
    background: var(--accent);
    display: flex;
    align-items: center;
    justify-content: center;
    flex: none;
  }
  .contact-icon svg { width: 10px; height: 10px; }

  .accent-band {
    position: absolute;
    left: 0;
    right: 0;
    bottom: 14px;
    height: 14px;
    background: linear-gradient(90deg, var(--accent-dark), var(--accent));
  }
</style>
</head>
<body>
<main class="stage">

  <section class="card card--back" aria-label="Card back with contact details">
    <div class="brand">
      <div class="brand-circle"></div>
      <div class="brand-name">Tom Varulek</div>
    </div>

    <div class="contact">
      <p class="contact-name">Tom Varulek</p>
      <p class="contact-role">Web Developer</p>
      <ul class="contact-list">
        <li class="contact-item">
          <span class="contact-icon">
            <svg viewBox="0 0 10 10"><path d="M2 1 L3.6 1 L4.2 3 L3.2 3.8 Q4 5.8 6.2 6.8 L7 5.8 L9 6.4 L9 8 Q9 9 8 9 Q1 8.5 1 2 Q1 1 2 1 Z" fill="#0c0c0c"/></svg>
          </span>
          570-614-3098
        </li>
        <li class="contact-item">
          <span class="contact-icon">
            <svg viewBox="0 0 10 10"><rect x="1" y="2.2" width="8" height="5.6" fill="none" stroke="#0c0c0c" stroke-width="1.1"/><path d="M1 2.4 L5 5.6 L9 2.4" fill="none" stroke="#0c0c0c" stroke-width="1.1"/></svg>
          </span>
          tomvarulek@quillbox.net
        </li>
        <li class="contact-item">
          <span class="contact-icon">
            <svg viewBox="0 0 10 10"><circle cx="5" cy="5" r="3.8" fill="none" stroke="#0c0c0c" stroke-width="1"/><ellipse cx="5" cy="5" rx="1.6" ry="3.8" fill="none" stroke="#0c0c0c" stroke-width="0.9"/><path d="M1.2 5 H8.8" stroke="#0c0c0c" stroke-width="0.9"/></svg>
          </span>
          www.tomvarulek.net
        </li>
      </ul>
    </div>

    <div class="accent-band"></div>
  </section>

  <section class="card card--front" aria-label="Card front with mark and name">
    <div class="brand">
      <div class="brand-circle"></div>
      <div class="brand-name">Tom Varulek</div>
    </div>
  </section>

</main>
</body>
</html>
```